Business Card Design Project

We are not a new company, but renamed to "Vantorin Kitchens" last year. We specialize in modern high-end cabinetry imports. We would like to communicate a sense of quality and cutting edge technology. Ideally the design would incorporate our logo colors, silver, red and preferably a black, matte background. Though we are open to suggestions.
Logo is attached.
Edit: I have attached rough drafts of the previous cards, this way you will have all necessary content that needs to go on the cards.
Updates
Project Deadline Extended
Reason: We have received a lot of great designs, but due to the sheer number we couldn't respond to all. We will extend the deadline for another 7 days to finalize and provide feedback to designers.
Thank you for your hard work!
Industry/Entity Type
Business
Look and feel
Each slider illustrates characteristics of the customer's brand and the style your logo design should communicate.

```html
<!DOCTYPE html>
<html lang="en">
<head>
<meta charset="utf-8">
<title>Vantorin Kitchens – Business Cards</title>
<link href="https://fonts.googleapis.com/css2?family=Arimo:wght@400;700&family=PT+Sans&display=swap" rel="stylesheet">
<style>
  :root {
    --stage: #e6e2dc;
    --label: #2a2521;
    --card-matte: #1c1c1d;
    --card-matte-edge: #0c0c0c;
    --card-black: #050505;
    --ink: #ffffff;
    --silver: #c9c9c9;
    --rule: #4a4a4a;
    --perf-light: #5a5a5a;
  }
  * { margin: 0; padding: 0; box-sizing: border-box; }
  html, body { width: 1200px; height: 788px; overflow: hidden; }
  body {
    position: relative;
    background: var(--stage);
    font-family: "Arimo", Arial, sans-serif;
    color: var(--ink);
  }
  .view-label {
    position: absolute;
    font-family: "PT Sans", sans-serif;
    font-size: 22px;
    color: var(--label);
    transform: translateX(-50%);
  }
  .card {
    position: absolute;
    border-radius: 20px;
    overflow: hidden;
    box-shadow: 0 4px 14px rgba(0,0,0,.35);
  }
  .card--matte {
    background: radial-gradient(ellipse at 50% 45%, #2a2a2b 0%, var(--card-matte) 55%, var(--card-matte-edge) 100%);
  }
  .card--black { background: var(--card-black); }

  .wordmark {
    position: absolute;
    display: flex;
    align-items: center;
    gap: 10px;
    transform: translate(-50%, -50%);
    white-space: nowrap;
    color: var(--silver);
    font-weight: 700;
    letter-spacing: 1px;
    text-transform: uppercase;
  }
  .wordmark__square { background: var(--silver); flex: none; }
  .wordmark--small { font-size: 21px; }
  .wordmark--small .wordmark__square { width: 16px; height: 16px; }
  .wordmark--large { font-size: 31px; }
  .wordmark--large .wordmark__square { width: 24px; height: 24px; }

  .contact {
    position: absolute;
    left: 302px;
    top: 27px;
    bottom: 22px;
    border-left: 1px solid var(--rule);
    padding-left: 13px;
    width: 210px;
  }
  .contact__name { font-size: 18px; font-weight: 700; text-transform: uppercase; line-height: 1.15; margin-top: 6px; }
  .contact__name--light { font-weight: 400; }
  .contact__role { font-size: 15px; line-height: 1.2; }
  .contact__role--small { font-size: 13px; }
  .contact__block {
    border-top: 1px solid var(--rule);
    margin-left: -13px;
    padding-left: 13px;
    font-size: 13px;
    line-height: 1.45;
  }
  .contact__block--phones { margin-top: 15px; padding-top: 19px; padding-bottom: 12px; width: 162px; }
  .contact__block--phones p { white-space: nowrap; }
  .contact__block--email { padding: 11px 0 11px 13px; width: 182px; }
  .contact__block--address { padding-top: 11px; line-height: 1.3; width: 182px; }
  .contact strong { font-weight: 700; }

  .perforation {
    position: absolute;
  }
  .perforation--top {
    left: 0; top: 0; width: 260px; height: 90px;
    background: radial-gradient(ellipse at 55% 30%, var(--perf-light) 0%, #2a2a2a 40%, transparent 75%);
  }
  .perforation--bottom {
    right: 0; bottom: 0; width: 250px; height: 90px;
    background: radial-gradient(ellipse at 40% 70%, var(--perf-light) 0%, #2a2a2a 40%, transparent 75%);
  }
</style>
</head>
<body>
  <span class="view-label" style="left:307px;top:22px">front</span>
  <span class="view-label" style="left:890px;top:22px">front-1</span>
  <span class="view-label" style="left:314px;top:406px">back</span>
  <span class="view-label" style="left:892px;top:406px">Back - 1</span>

  <section class="card card--matte" style="left:53px;top:71px;width:525px;height:300px">
    <div class="wordmark wordmark--small" style="left:157px;top:145px">
      <span class="wordmark__square"></span>Vantorin Kitchens
    </div>
    <div class="contact">
      <h1 class="contact__name">Marek Dolan</h1>
      <p class="contact__role">President</p>
      <div class="contact__block contact__block--phones">
        <p><strong>phone</strong> : 555.210.4180</p>
        <p><strong>cell</strong> : 555.210.7732</p>
        <p><strong>fax</strong> : 555.210.4195</p>
      </div>
      <div class="contact__block contact__block--email">marek@vantorinkitchens.ca</div>
      <div class="contact__block contact__block--address">1820 - 48 Ave., Calder Ridge<br>AB T0X 4K2</div>
    </div>
  </section>

  <section class="card card--black" style="left:628px;top:71px;width:525px;height:300px">
    <div class="wordmark wordmark--small" style="left:157px;top:145px">
      <span class="wordmark__square"></span>Vantorin Kitchens
    </div>
    <div class="contact">
      <h1 class="contact__name contact__name--light">Tomas Dolan</h1>
      <p class="contact__role contact__role--small">Director</p>
      <div class="contact__block contact__block--phones">
        <p><strong>phone</strong> : 555.210.4180</p>
        <p><strong>cell</strong> : 555.210.6641</p>
        <p><strong>fax</strong> : 555.210.4195</p>
      </div>
      <div class="contact__block contact__block--email">tomas@vantorinkitchens.ca</div>
      <div class="contact__block contact__block--address">1820 - 48 Ave., Calder Ridge<br>AB T0X 4K2</div>
    </div>
  </section>

  <section class="card card--matte" style="left:57px;top:447px;width:523px;height:298px">
    <div class="wordmark wordmark--large" style="left:262px;top:150px">
      <span class="wordmark__square"></span>Vantorin Kitchens
    </div>
  </section>

  <section class="card card--black" style="left:625px;top:446px;width:524px;height:300px">
    <div class="perforation perforation--top" role="img" aria-label="Perforated metal texture"></div>
    <div class="perforation perforation--bottom" role="img" aria-label="Perforated metal texture"></div>
    <div class="wordmark wordmark--large" style="left:265px;top:155px">
      <span class="wordmark__square"></span>Vantorin Kitchens
    </div>
  </section>
</body>
</html>
```